Buch-Umschlag
Zielgruppe
Wir sind eine Weiterbildungsfirma mit der Zielgruppe Unternehmer, Selbstständige, Führungskräfte und Vertriebler.
Aufgabenstellung
Es soll dynamisch, elegant und professionell wirken. Der Titel muss gut lesbar sein.
(Wir haben einen Velimo-Bild-Account auf Abo-Basis.)
Der Titel lautet neu: Die Halvek-Prinzipien für starke Ziele

```html
<!DOCTYPE html>
<html lang="de">
<head>
<meta charset="utf-8">
<title>Die Halvek-Prinzipien für starke Ziele – Buchumschlag</title>
<link rel="stylesheet" href="https://fonts.googleapis.com/css2?family=Bebas+Neue&family=Jost:wght@500;600&display=swap">
<style>
  :root {
    --stage: #c2c2c2;
    --navy-light: #2b3487;
    --navy-dark: #231c5c;
    --gold: #d9ab2f;
    --white: #ffffff;
    --paper: #f3f3f3;
    --ink-blue: #2b3590;
    --badge-ink: #1d1a3e;
  }
  html, body {
    margin: 0;
    width: 1195px;
    height: 1200px;
    overflow: hidden;
    background: var(--stage);
  }
  .book-cover {
    position: absolute;
    left: 225px;
    top: 40px;
    width: 744px;
    height: 1120px;
    display: block;
  }
  .title-display { font-family: "Bebas Neue", "Oswald", sans-serif; }
  .body-type { font-family: "Jost", "Futura", sans-serif; }
</style>
</head>
<body>
<svg class="book-cover" viewBox="0 0 971 1463" xmlns="http://www.w3.org/2000/svg" role="img" aria-label="Buchumschlag: Die Halvek-Prinzipien für starke Ziele von Jonas T. Halvek">
  <defs>
    <linearGradient id="cover-navy" x1="0" y1="0" x2="1" y2="0.3">
      <stop offset="0" stop-color="var(--navy-light)"/>
      <stop offset="1" stop-color="var(--navy-dark)"/>
    </linearGradient>
    <linearGradient id="spine-shade" x1="0" y1="0" x2="1" y2="0">
      <stop offset="0" stop-color="#ffffff" stop-opacity="0.12"/>
      <stop offset="0.5" stop-color="#ffffff" stop-opacity="0.2"/>
      <stop offset="1" stop-color="#ffffff" stop-opacity="0"/>
    </linearGradient>
  </defs>

  <!-- cover background -->
  <rect class="cover-navy" width="971" height="1463" fill="url(#cover-navy)"/>
  <path class="torn-paper" fill="var(--paper)"
    d="M0 980 L40 974 L80 978 L120 970 L160 966 L175 958 L190 968 L240 964 L290 972 L340 962 L390 966 L440 960 L480 964 L520 958 L560 966 L610 962 L660 970 L700 966 L740 974 L790 968 L830 976 L880 974 L930 980 L971 976 L971 1463 L0 1463 Z"/>
  <rect class="spine-shade" width="60" height="1463" fill="url(#spine-shade)"/>

  <!-- author -->
  <text class="body-type author-name" x="485" y="133" text-anchor="middle" font-size="66" font-weight="600" letter-spacing="9" fill="var(--gold)">JONAS T. HALVEK</text>

  <!-- title -->
  <text class="title-display title-article" x="474" y="465" text-anchor="middle" font-size="121" fill="var(--gold)">DIE</text>
  <text class="title-display title-name" x="120" y="745" font-size="371" textLength="735" lengthAdjust="spacingAndGlyphs" fill="var(--white)">HALVEK</text>
  <text class="title-display title-keyword" x="120" y="937" font-size="260" textLength="735" lengthAdjust="spacingAndGlyphs" fill="var(--gold)">PRINZIPIEN</text>
  <text class="title-display title-subline" x="120" y="1095" font-size="114" textLength="738" lengthAdjust="spacingAndGlyphs" fill="var(--gold)">FÜR STARKE ZIELE</text>

  <!-- bonus badge -->
  <g class="bonus-badge" transform="translate(782 325)">
    <g fill="var(--gold)">
      <circle r="118"/>
      <rect x="-92" y="-92" width="184" height="184" transform="rotate(0)"/>
      <rect x="-92" y="-92" width="184" height="184" transform="rotate(7.5)"/>
      <rect x="-92" y="-92" width="184" height="184" transform="rotate(15)"/>
      <rect x="-92" y="-92" width="184" height="184" transform="rotate(22.5)"/>
      <rect x="-92" y="-92" width="184" height="184" transform="rotate(30)"/>
      <rect x="-92" y="-92" width="184" height="184" transform="rotate(37.5)"/>
      <rect x="-92" y="-92" width="184" height="184" transform="rotate(45)"/>
      <rect x="-92" y="-92" width="184" height="184" transform="rotate(52.5)"/>
      <rect x="-92" y="-92" width="184" height="184" transform="rotate(60)"/>
      <rect x="-92" y="-92" width="184" height="184" transform="rotate(67.5)"/>
      <rect x="-92" y="-92" width="184" height="184" transform="rotate(75)"/>
      <rect x="-92" y="-92" width="184" height="184" transform="rotate(82.5)"/>
    </g>
    <g class="title-display" transform="rotate(18)" text-anchor="middle" font-size="46">
      <text x="-4" y="-52" fill="var(--badge-ink)">GRATIS DAZU:</text>
      <text x="-10" y="-8" fill="var(--white)">DIE HÖRBUCH-</text>
      <text x="-18" y="36" fill="var(--white)">AUSGABE</text>
      <text x="-30" y="78" font-size="40" fill="var(--white)">ALS MP3</text>
    </g>
  </g>

  <!-- reading note -->
  <g class="body-type reading-note" text-anchor="middle" font-size="32" font-weight="600" fill="var(--ink-blue)">
    <text x="481" y="1283">Für das Lesen dieses Buches brauchen Sie</text>
    <text x="481" y="1327">nur etwa zwei Stunden – oder an zwölf</text>
    <text x="481" y="1370">Tagen jeweils zehn Minuten.</text>
  </g>
</svg>
</body>
</html>
```